Venture Capital firm needs modern business cards

We are a Venture Capital firm within financial services/Asset management. The industry generally has basic business cards with black, blue and maybe green/yellow design elements.
Our firm has a four-colour swoosh logo. We are based in London and want to stand out, just a little bit!, from the crowd. Our company is called LORV Investments and the 'C' stands for collaboration thus using makerswarm is a natural portal for our business card design competition. Our logo came via makerswarm too!
We use 'Venture Partner in Asset Management' as our tagline and this is Trademark registered. We operate in a conservative industry and we should not overstep our mark. The logo is colorful as it is and therefore the rest of the design should not be too fanciful.
The objective is twofold: make our logo element stick and memorable with our audience, whilst representing a conservative yet young image.
Updates
The Business Card obviously needs a field for Name, Surname, Job Title, Adress fields: Street, City, Postcode, Country, telefone and cell number, website address, etc.
We have uploaded the ai file. We trust that these are OK. If not, please advise.
Reason: We have have been busy with a client engagement. We will set the project as Guaranteed in return for the troubles we cause. Apologies for the confusion.
Thank you all for these great and creative design suggestions. The team is very happy with a number of your ideas! We will be in touch tomorrow to give individual feedback before the project closes on Friday. We look forward to working with some of you to narrow down your creations. Thank you, LORV Investments team.
All,
Target Market(s)
Financial Services Professionals, Investors, Media, 35-70 years, mainly male, well educated
Industry/Entity Type
Conservative
Requirements
Must have
- We must make use of our logo and potential tagline 'Venture Partner in Asset Management' as we are establishing a new Brand and new company in the market.
We can use 'LORV', 'LORV Investments', and 'LORV Investments'+tagline 'Venture Partner in Asset Management' or simply the four-colour swoosh plus the name of the company as part of the text. (see files)
All design elements are available in black or grey-scale if required. (grey scale swoosh attached).
Due to regulation we must have the following wording on the card in small print 'LORV Investments is an Appointed Representative of Bramwell Holdings Partnership Limited, which is authorised by the Monetary Oversight Board'.
Nice to have
- We would consider designs that make use of different printing techniques such embossing/debossing, UV spot etc.
We attach our colour palette in the files section for your reference.
Should not have
- The font we use for our company name is 'EXO' so do not use a font style that clashes with the corporate fonts, please.
Do not use other design elements than the ones we provide in the file library as part of this project.

```html
<!DOCTYPE html>
<html lang="en">
<head>
<meta charset="utf-8">
<title>LORV Investments – Business Card</title>
<link rel="stylesheet" href="https://fonts.googleapis.com/css2?family=Arimo:wght@400;700&display=swap">
<style>
  :root {
    --page: #ffffff;
    --card-white: #ffffff;
    --card-grey: #656767;
    --accent-pink: #e5307a;
    --accent-teal: #8fcfdc;
    --ink-light: #ffffff;
    --ink-dark: #222222;
    --card-edge: #d6d6d6;
  }
  * { box-sizing: border-box; margin: 0; padding: 0; }
  html, body {
    width: 1200px; height: 554px; overflow: hidden;
    background: var(--page);
    font-family: "Arimo", Arial, sans-serif;
  }
  .canvas { position: relative; width: 1200px; height: 554px; }

  .card {
    position: absolute; top: 110px;
    width: 520px; height: 296px;
    box-shadow: 0 10px 14px -8px rgba(0,0,0,0.35);
  }
  .card--front {
    left: 60px; background: var(--card-white);
    border: 1px solid var(--card-edge);
  }
  .card--back { left: 620px; background: var(--card-grey); color: var(--ink-light); }

  /* front */
  .holder { position: absolute; left: 40px; top: 118px; text-align: right; }
  .holder__name { font-size: 27px; color: var(--accent-pink); line-height: 1.1; }
  .holder__title { font-size: 16px; color: var(--accent-pink); margin-top: 4px; }
  .brand-mark {
    position: absolute; left: 260px; top: 24px; width: 230px; height: 248px;
    display: flex; align-items: center; justify-content: center; gap: 14px;
  }
  .brand-mark__dot { width: 34px; height: 34px; border-radius: 50%; background: var(--accent-teal); }
  .brand-mark__name { font-size: 64px; color: var(--accent-pink); letter-spacing: 2px; }

  /* back */
  .brand-line {
    position: absolute; right: 38px; top: 26px; text-align: left;
  }
  .brand-line__row { display: flex; align-items: center; gap: 8px; }
  .brand-line__dot { width: 22px; height: 22px; border-radius: 50%; background: var(--accent-teal); }
  .brand-line__name { font-size: 40px; color: var(--ink-light); letter-spacing: 1px; line-height: 1; }
  .brand-line__tagline { font-size: 7px; color: var(--ink-light); margin: 3px 0 0 30px; }

  .contacts { position: absolute; left: 28px; top: 116px; list-style: none; }
  .contacts li {
    display: flex; align-items: flex-start; gap: 12px;
    font-size: 15px; line-height: 1.25; margin-bottom: 10px;
  }
  .contacts svg { width: 16px; height: 16px; flex: none; margin-top: 1px; }

  .legal {
    position: absolute; left: 6px; bottom: 6px; font-size: 8.6px; white-space: nowrap;
  }
  .legal--side {
    left: auto; bottom: auto; right: -4px; top: 148px;
    transform: translate(50%, -50%) rotate(-90deg); transform-origin: center;
    right: 10px;
  }

  .note {
    position: absolute; left: 18px; top: 528px;
    font-size: 15px; color: var(--ink-dark);
  }
  .note b { font-weight: 700; }
</style>
</head>
<body>
<main class="canvas">

  <section class="card card--front" aria-label="Card front">
    <div class="holder">
      <p class="holder__name">Martin Hale</p>
      <p class="holder__title">Chairman</p>
    </div>
    <div class="brand-mark">
      <span class="brand-mark__dot"></span>
      <span class="brand-mark__name">LORV</span>
    </div>
  </section>

  <section class="card card--back" aria-label="Card back">
    <div class="brand-line">
      <div class="brand-line__row">
        <span class="brand-line__dot"></span>
        <span class="brand-line__name">LORV</span>
      </div>
      <p class="brand-line__tagline">Venture Partner in Asset Management</p>
    </div>

    <ul class="contacts">
      <li>
        <svg viewBox="0 0 16 16" fill="none" stroke="#fff" stroke-width="1.2"><rect x="1.5" y="3.5" width="13" height="9"/><path d="M1.5 3.5 8 9l6.5-5.5"/></svg>
        martin@lorvinvestments.com
      </li>
      <li>
        <svg viewBox="0 0 16 16" fill="none" stroke="#fff" stroke-width="1.2"><circle cx="8" cy="8" r="6.5"/><ellipse cx="8" cy="8" rx="2.8" ry="6.5"/><path d="M1.5 8h13"/></svg>
        www.lorvinvestments.com
      </li>
      <li>
        <svg viewBox="0 0 16 16" fill="none" stroke="#fff" stroke-width="1.2"><path d="M3 2l3 3-1.5 2c1 2 2.5 3.5 4.5 4.5L11 10l3 3-2 2C7 14 2 9 1 4z"/></svg>
        +1 (800) 555-0142
      </li>
      <li>
        <svg viewBox="0 0 16 16" fill="none" stroke="#fff" stroke-width="1.2"><rect x="4" y="1.5" width="8" height="13" rx="1"/><path d="M7 12.5h2"/></svg>
        +1 (800) 555-0142
      </li>
      <li>
        <svg viewBox="0 0 16 16" fill="none" stroke="#fff" stroke-width="1.2"><path d="M1.5 8 8 2l6.5 6M3.5 6.5V14h9V6.5M6.5 14v-4h3v4"/></svg>
        <span>12 Harbour Lane, 7 Elmwood Court,<br>London, United Kingdom NW4 2QT</span>
      </li>
    </ul>

    <p class="legal">'LORV Investments is an Appointed Representative of Bramwell Holdings Partnership Limited, which is</p>
    <p class="legal legal--side">authorised by the Monetary Oversight Board'.</p>
  </section>

  <p class="note">• Note : <b>LORV</b> on the grey side can be UV spot</p>
</main>
</body>
</html>
```